Birchline Septic Solutions

Would like to see some single sided ones but would also like to see some double sided with one sided only being the logo. Owners name is Colin Vandro. Phone number is 555-214-0387
Services are pumping, inspections, installs, and repairs

Contact Information for Business Card

555-241-0387 Colin Vandro Greenfield, OH

```html
<!DOCTYPE html>
<html lang="en">
<head>
<meta charset="utf-8">
<title>Birchline Septic Solutions – Business Cards</title>
<link href="https://fonts.googleapis.com/css2?family=Lato:wght@400;700;900&display=swap" rel="stylesheet">
<style>
  :root {
    --stage: #2b2d30;
    --card-white: #ffffff;
    --card-black: #1f1f1f;
    --teal: #22b8b0;
    --ink: #151515;
    --ink-soft: #5a5a5a;
    --on-dark: #ffffff;
  }
  * { box-sizing: border-box; margin: 0; padding: 0; }
  html, body { width: 1200px; height: 952px; overflow: hidden; }
  body {
    background: var(--stage);
    font-family: "Lato", Arial, sans-serif;
    display: flex;
    flex-direction: column;
    align-items: center;
    justify-content: center;
    gap: 64px;
  }
  .card {
    position: relative;
    width: 560px;
    height: 320px;
    border-radius: 20px;
    overflow: hidden;
  }

  /* Front */
  .card--front { background: var(--card-white); color: var(--ink); }
  .brand {
    position: absolute;
    display: flex;
    align-items: center;
    gap: 12px;
  }
  .brand__mark { width: 18px; height: 18px; background: var(--teal); flex: none; }
  .brand__name {
    font-weight: 900;
    text-transform: uppercase;
    line-height: 1.05;
    letter-spacing: 1px;
  }
  .card--front .brand { left: 36px; top: 70px; width: 250px; }
  .card--front .brand__name { font-size: 27px; color: var(--ink); }

  .contact { position: absolute; left: 300px; top: 44px; width: 240px; }
  .contact__name {
    color: var(--teal);
    font-weight: 900;
    font-size: 27px;
    text-transform: uppercase;
    letter-spacing: 0.5px;
    line-height: 1;
  }
  .contact__role { color: var(--ink-soft); font-size: 14px; margin-top: 4px; }
  .contact__rule { width: 48px; height: 2px; background: var(--ink); margin: 10px 0 12px; }
  .contact__list { list-style: none; }
  .contact__item {
    display: flex;
    align-items: flex-start;
    gap: 8px;
    font-size: 12.5px;
    color: var(--ink-soft);
    line-height: 1.3;
    margin-bottom: 7px;
  }
  .contact__icon { width: 16px; height: 16px; flex: none; border-radius: 3px; background: var(--teal); margin-top: 1px; }
  .contact__icon--dark { background: var(--ink); }

  .services {
    position: absolute;
    left: 0; right: 0; bottom: 28px;
    height: 46px;
    background: var(--teal);
    color: var(--on-dark);
    display: flex;
    align-items: center;
    padding-left: 26px;
    font-size: 18px;
    text-transform: uppercase;
    letter-spacing: 0.3px;
    white-space: nowrap;
  }

  /* Back */
  .card--back { background: var(--card-black); }
  .card--back .brand { left: 0; right: 0; top: 108px; justify-content: center; }
  .card--back .brand__name { font-size: 32px; color: var(--on-dark); text-align: center; }
  .back__line { position: absolute; left: 0; right: 0; bottom: 42px; height: 1px; background: var(--teal); }
</style>
</head>
<body>

  <section class="card card--front" aria-label="Business card front">
    <div class="brand">
      <span class="brand__mark"></span>
      <span class="brand__name">Birchline<br>Septic Solutions</span>
    </div>

    <div class="contact">
      <h1 class="contact__name">Colin Vandro</h1>
      <p class="contact__role">Managing Director</p>
      <div class="contact__rule"></div>
      <ul class="contact__list">
        <li class="contact__item">
          <svg class="contact__icon contact__icon--dark" viewBox="0 0 16 16"><path d="M8 3.2a3 3 0 0 0-3 3c0 2.2 3 5.6 3 5.6s3-3.4 3-5.6a3 3 0 0 0-3-3zm0 4.1a1.1 1.1 0 1 1 0-2.2 1.1 1.1 0 0 1 0 2.2z" fill="#fff"/></svg>
          <span>1720 Orchard Ridge Road<br>Greenfield, OH 45123</span>
        </li>
        <li class="contact__item">
          <svg class="contact__icon" viewBox="0 0 16 16"><path d="M5.2 3.5l1.6 2.2-1 1.1c.6 1.3 1.6 2.3 2.9 2.9l1.1-1 2.2 1.6-.8 1.9C7.3 12 4 8.7 3.3 4.3z" fill="#fff"/></svg>
          <span>555-241-0387</span>
        </li>
        <li class="contact__item">
          <svg class="contact__icon" viewBox="0 0 16 16"><rect x="3.2" y="4.8" width="9.6" height="6.6" fill="none" stroke="#fff" stroke-width="1.2"/><path d="M3.4 5l4.6 3.6L12.6 5" fill="none" stroke="#fff" stroke-width="1.2"/></svg>
          <span>office@birchlineseptic.com</span>
        </li>
        <li class="contact__item">
          <svg class="contact__icon" viewBox="0 0 16 16"><path d="M5 4l6.5 3-2.8 1 2 2.6-1 .8-2-2.6L6 11.5z" fill="#fff"/></svg>
          <span>www.birchlineseptic.com</span>
        </li>
      </ul>
    </div>

    <div class="services">• Pumping • Inspections • Installs • Repairs</div>
  </section>

  <section class="card card--back" aria-label="Business card back">
    <div class="brand">
      <span class="brand__mark"></span>
      <span class="brand__name">Birchline<br>Septic Solutions</span>
    </div>
    <div class="back__line"></div>
  </section>

</body>
</html>
```